Ridgeway Mining Solutions Business Card

Ridgeway Mining Solutions is a company that provides consulting services to the Mining Industry.

Whilst Ridgeway Mining Solutions is an Australian based company its client base is the global mining industry.

The essence of Ridgeway Mining Solutions is its a can do organisation that can make a difference to its clients by providing quality assistance and form lasting relationships.
Updates

Target Market(s)

The global Mining Industry.

Industry/Entity Type

Mining

Font styles to use
Serif

Colors

Designer to choose colors to be used in the design.

Requirements
Nice to have
• My thinking is the card would look good in black given the logo.

I would like to see written on the back side of the card " Providing Metallurgical, Management and Corporate Services to the Mining Industry"

```html
<!DOCTYPE html>
<html lang="en">
<head>
<meta charset="utf-8">
<title>Ridgeway Mining Solutions – Business Card</title>
<link href="https://fonts.googleapis.com/css2?family=Libre+Baskerville:wght@400;700&family=Cinzel:wght@400;600&display=swap" rel="stylesheet">
<style>
  :root {
    --backdrop: #d9d8d6;
    --card-white: #ffffff;
    --ink-black: #050505;
    --brand-gold: #f2b22c;
    --text-dark: #111111;
    --shadow: rgba(0, 0, 0, 0.28);
  }
  * { margin: 0; padding: 0; box-sizing: border-box; }
  html, body { width: 1200px; height: 864px; overflow: hidden; }
  body {
    background: linear-gradient(160deg, #e6e5e3 0%, var(--backdrop) 60%, #c9c7c4 100%);
    position: relative;
    font-family: "Libre Baskerville", Georgia, serif;
  }
  .card {
    position: absolute;
    width: 620px;
    height: 354px;
    background: var(--card-white);
    overflow: hidden;
    box-shadow: 0 14px 30px var(--shadow);
  }
  .card svg.card-art { position: absolute; inset: 0; width: 100%; height: 100%; }

  /* Back card */
  .card-back { left: 500px; top: 48px; }
  .back-brand {
    position: absolute;
    left: 0; right: 0;
    top: 112px;
    text-align: center;
    color: var(--brand-gold);
    font-weight: 700;
    line-height: 1;
  }
  .brand-name { display: block; font-size: 34px; letter-spacing: 1px; }
  .brand-sub { display: block; font-size: 12px; letter-spacing: 3px; margin-top: 8px; text-transform: uppercase; }
  .back-tagline {
    position: absolute;
    left: 0; right: 0;
    top: 214px;
    text-align: center;
    color: var(--card-white);
    font-family: "Cinzel", "Times New Roman", serif;
    font-size: 14px;
    line-height: 1.55;
    letter-spacing: 0.5px;
  }

  /* Front card */
  .card-front { left: 80px; top: 462px; }
  .front-brand {
    position: absolute;
    left: 44px;
    top: 128px;
    color: var(--brand-gold);
    font-weight: 700;
    line-height: 1;
  }
  .contact {
    position: absolute;
    left: 402px;
    top: 70px;
    color: var(--text-dark);
  }
  .contact-name { font-size: 22px; margin: 0 0 34px 36px; letter-spacing: 0.5px; }
  .contact-list { list-style: none; }
  .contact-item {
    display: flex;
    align-items: center;
    gap: 14px;
    font-size: 15px;
    height: 30px;
  }
  .contact-item svg { width: 16px; height: 16px; flex: none; }
</style>
</head>
<body>

  <section class="card card-back" aria-label="Back of business card">
    <svg class="card-art" viewBox="0 0 620 354" aria-hidden="true">
      <ellipse cx="322" cy="172" rx="176" ry="212" fill="none" stroke="var(--ink-black)" stroke-width="4"/>
      <ellipse cx="322" cy="172" rx="166" ry="204" fill="var(--ink-black)"/>
      <ellipse cx="322" cy="172" rx="156" ry="196" fill="none" stroke="var(--card-white)" stroke-width="3"/>
    </svg>
    <div class="back-brand">
      <span class="brand-name">RIDGEWAY</span>
      <span class="brand-sub">Mining Solutions</span>
    </div>
    <p class="back-tagline">We provide consulting services<br>to the Mining Industry..</p>
  </section>

  <section class="card card-front" aria-label="Front of business card">
    <svg class="card-art" viewBox="0 0 620 354" aria-hidden="true">
      <path d="M0 0 H340 C 410 120 370 270 230 354 H0 Z" fill="var(--ink-black)"/>
    </svg>
    <div class="front-brand">
      <span class="brand-name">RIDGEWAY</span>
      <span class="brand-sub">Mining Solutions</span>
    </div>
    <div class="contact">
      <p class="contact-name">Your Name</p>
      <ul class="contact-list">
        <li class="contact-item">
          <svg viewBox="0 0 16 16"><path d="M8 1a4.5 4.5 0 0 0-4.5 4.5C3.5 9 8 15 8 15s4.5-6 4.5-9.5A4.5 4.5 0 0 0 8 1zm0 6.3a1.8 1.8 0 1 1 0-3.6 1.8 1.8 0 0 1 0 3.6z" fill="var(--text-dark)"/></svg>
          <span>Your address</span>
        </li>
        <li class="contact-item">
          <svg viewBox="0 0 16 16"><path d="M4 1.5l2.2 2.8-1.3 1.6c.8 2 2.5 3.7 4.5 4.5l1.6-1.3 2.8 2.2-1.5 2.2C7.5 13.3 2.7 8.5 2 3z" fill="var(--text-dark)"/></svg>
          <span>000 0000 0000</span>
        </li>
        <li class="contact-item">
          <svg viewBox="0 0 16 16"><rect x="1.5" y="3.5" width="13" height="9" fill="none" stroke="var(--text-dark)" stroke-width="1.4"/><path d="M1.5 3.5 8 9l6.5-5.5" fill="none" stroke="var(--text-dark)" stroke-width="1.4"/></svg>
          <span>inof@email.com</span>
        </li>
        <li class="contact-item">
          <svg viewBox="0 0 16 16" fill="none" stroke="var(--text-dark)" stroke-width="1.2"><circle cx="8" cy="8" r="6.5"/><ellipse cx="8" cy="8" rx="3" ry="6.5"/><path d="M1.5 8h13M2.5 4.8h11M2.5 11.2h11"/></svg>
          <span>www.yourwebsite.com</span>
        </li>
      </ul>
    </div>
  </section>

</body>
</html>
```